Moxy Fen needs some awesome stationary

Do you have what it takes to get my brand? You either do or you don't, have a crack at a design and you my just win my business.

I don't want to waste your or my time, so put your creative genius on either a business card or envelope.

I however need a package of stationary that follows the same brand. I will message you to complete the remaining should I like your first submission.

Here is what I need, have a go!

Basically I need the following for my small business based in melbourne.
- Letterhead (printer ready and MS Word)
- Business Card
- Compliments Slip
- Envelope
- Proposal Cover Page (MS Word only)
- Presentation Folder
- Marbled Fox Cards
- Student Name Tent
- Index Cards
- Vell-Ka

I am establishing the brand and it must be modern, professional but also relaxed; that is not formal and not corporate. It represents a company are leaders, but small enough to care and operate like a bunch of friends. We are bringing people and conversations back to business, and turfing out all the bureaucracy and crazy and wasteful procedures. Its about "lets talk and figure it out together and find even better ways".

Target Market(s)

Mainly companies that build software products, but Agile practices are used in many other industries (even graphic design projects)

Industry/Entity Type

Information Technology

Font styles to use
Sans Serif

Colors
3176b5
aaaaaa

Requirements
Must have
• I like curves and circles and not boxes or rectangles.
• I want a colour rich design with my brand colours, but it must be balanced.
• I want more modern than traditional, but simple modern
Should not have
• Not corporate
• Please don't waste my time if your not going to think about it.
• Don't mess with my primary logo
• Don't change my colours
• Don't overlay logo on image

```html
<!DOCTYPE html>
<html lang="en">
<head>
<meta charset="utf-8">
<title>Moxy Fen — Presentation Folder Cover</title>
<link rel="stylesheet" href="https://fonts.googleapis.com/css2?family=Source+Sans+3:wght@400;700&display=swap">
<style>
  :root {
    --brand-blue: #3a5e99;
    --brand-grey: #9aa1ad;
    --paper: #ececec;
    --ink-grey: #4d4f54;
    --white: #ffffff;
  }
  html, body {
    margin: 0;
    padding: 0;
    width: 1018px;
    height: 1200px;
    overflow: hidden;
    background: var(--paper);
    font-family: "Source Sans 3", sans-serif;
  }
  .folder-cover {
    position: relative;
    width: 1018px;
    height: 1200px;
    background: var(--paper);
  }
  .brand-mark {
    position: absolute;
    top: 60px;
    left: 0;
    width: 100%;
    display: flex;
    flex-direction: column;
    align-items: center;
  }
  .brand-mark__dot {
    width: 96px;
    height: 96px;
    border-radius: 50%;
    background: var(--brand-blue);
  }
  .brand-mark__name {
    margin-top: 14px;
    font-size: 40px;
    font-weight: 700;
    color: var(--brand-blue);
    line-height: 1;
  }
  .contact {
    position: absolute;
    top: 1052px;
    left: 0;
    width: 100%;
    text-align: center;
    z-index: 2;
  }
  .contact__phone {
    font-size: 40px;
    font-weight: 700;
    color: var(--brand-blue);
    line-height: 1;
  }
  .contact__web {
    margin-top: 10px;
    font-size: 26px;
    font-weight: 400;
    letter-spacing: 3px;
    color: var(--ink-grey);
    line-height: 1;
  }
  .footer-swoosh {
    position: absolute;
    left: 0;
    top: 0;
    width: 1018px;
    height: 1200px;
  }
  .swoosh-grey { fill: var(--brand-grey); }
  .swoosh-blue { fill: var(--brand-blue); }
  .swoosh-line { fill: none; stroke: var(--white); stroke-width: 5; }
</style>
</head>
<body>
  <main class="folder-cover">
    <svg class="footer-swoosh" viewBox="0 0 1018 1200" aria-hidden="true">
      <path class="swoosh-grey" d="M380,1182 C700,1176 900,1112 1018,1010 L1018,1200 L380,1200 Z"/>
      <path class="swoosh-blue" d="M0,1078 C300,1170 650,1190 1018,1102 L1018,1200 L0,1200 Z"/>
      <path class="swoosh-line" d="M0,1078 C300,1170 650,1190 1018,1102"/>
    </svg>

    <header class="brand-mark">
      <div class="brand-mark__dot"></div>
      <div class="brand-mark__name">Moxy Fen</div>
    </header>

    <footer class="contact">
      <div class="contact__phone">13 000 MOXYF</div>
      <div class="contact__web">www.moxy-fen.com.au</div>
    </footer>
  </main>
</body>
</html>
```